Web Developer Needs a Business Card Design

I need a personal business card design that represents me as a web developer for potential employers. I would like the background to be a dark color on the front for contrast with my logo and name. The back will have all my information along with a smaller version of the logo. I want something with a modern look and feel, not too conservative. This will be used for potential employers and freelance work.

Industry/Entity Type

Business

Contact Information for Business Card

Front should have my logo and name. The back should have all my personal information which would include: name: Tom Varulek, phone: 570-614-3098, email: tomvarulek@quillbox.net, website url: www.tomvarulek.net, logo, web developer.

Font styles to use
Sans Serif

Requirements
Must have
• Must include my logo. The color palette base color will be the logo color.

```html
<!DOCTYPE html>
<html lang="en">
<head>
<meta charset="utf-8">
<title>Tom Varulek – Business Card</title>
<link href="https://fonts.googleapis.com/css2?family=Lato:wght@400;700&display=swap" rel="stylesheet">
<style>
  :root {
    --teal: #3b9a7f;
    --teal-soft: #63b39c;
    --ink: #1c1c1c;
    --paper: #ffffff;
    --night: #1e2a29;
    --on-night: #f2f5f4;
    --backdrop: #e7e7e7;
  }
  * { margin: 0; padding: 0; box-sizing: border-box; }
  html, body {
    width: 1200px; height: 720px; overflow: hidden;
    background: var(--backdrop);
    font-family: "Lato", sans-serif;
  }
  .stage { position: relative; width: 1200px; height: 720px; }
  .card {
    position: absolute; top: 205px;
    width: 540px; height: 309px;
    border-radius: 7px;
    overflow: hidden;
  }
  .card--back { left: 53px; background: var(--paper); }
  .card--front { left: 607px; background: var(--night); }

  .ring-deco { position: absolute; top: 0; }
  .card--back .ring-deco { left: 401px; }
  .card--front .ring-deco { left: -153px; }

  .brand {
    position: absolute; left: 31px; top: 21px;
    display: flex; align-items: center; gap: 12px;
  }
  .brand__mark {
    width: 64px; height: 64px; border-radius: 50%;
    border: 4px solid var(--teal);
  }
  .brand__name {
    font-size: 22px; font-weight: 700; letter-spacing: 2.6px;
    color: var(--teal);
  }

  .person { position: absolute; left: 33px; top: 133px; }
  .person__name { font-size: 20px; font-weight: 700; color: var(--teal); line-height: 1.2; }
  .person__role { font-size: 15px; color: var(--ink); line-height: 1.3; }

  .contacts { position: absolute; left: 31px; top: 200px; list-style: none; }
  .contacts li {
    display: flex; align-items: center; gap: 6px;
    font-size: 16px; color: var(--ink); line-height: 22px;
  }
  .contacts svg { width: 16px; height: 16px; fill: var(--teal); flex: none; }

  .front-mark {
    position: absolute; left: 288px; top: 78px;
    width: 154px; height: 154px; border-radius: 50%;
    border: 11px solid var(--teal);
    display: flex; align-items: center; justify-content: center;
  }
  .front-mark__name {
    font-size: 14px; font-weight: 700; letter-spacing: 1.5px; color: var(--teal);
  }
  .front-url {
    position: absolute; left: 250px; top: 243px; width: 230px;
    text-align: center; font-size: 17px; font-weight: 700; color: var(--on-night);
  }
  .front-url .accent { color: var(--teal-soft); }
</style>
</head>
<body>
<main class="stage">
  <section class="card card--back">
    <svg class="ring-deco" width="308" height="309" viewBox="0 0 308 309" aria-hidden="true">
      <circle cx="154" cy="154" r="134" fill="none" stroke="var(--teal-soft)" stroke-width="20"/>
    </svg>

    <div class="brand">
      <span class="brand__mark"></span>
      <span class="brand__name">TOM VARULEK</span>
    </div>

    <div class="person">
      <p class="person__name">Tom Varulek</p>
      <p class="person__role">Web Developer</p>
    </div>

    <ul class="contacts">
      <li>
        <svg viewBox="0 0 16 16" aria-hidden="true"><path d="M2 6c0-2 3-3.5 6-3.5S14 4 14 6v1h-3V5.6C10.3 5.3 9.2 5.2 8 5.2s-2.3.1-3 .4V7H2z M4 8h8l1.5 5h-11z M8 9.3a1.6 1.6 0 1 0 0 3.2 1.6 1.6 0 0 0 0-3.2z"/></svg>
        <span>570-614-3098</span>
      </li>
      <li>
        <svg viewBox="0 0 16 16" aria-hidden="true"><path d="M1 3.5h14v9H1z M2 4.5 8 9l6-4.5" stroke="#fff" stroke-width="1"/></svg>
        <span>tomvarulek@quillbox.net</span>
      </li>
      <li>
        <svg viewBox="0 0 16 16" aria-hidden="true"><circle cx="8" cy="8" r="7"/><path d="M1.5 8h13M8 1.2c2.2 2 2.2 11.6 0 13.6M8 1.2c-2.2 2-2.2 11.6 0 13.6M2.6 4.6h10.8M2.6 11.4h10.8" fill="none" stroke="#fff" stroke-width="1"/></svg>
        <span>www.tomvarulek.net</span>
      </li>
    </ul>
  </section>

  <section class="card card--front">
    <svg class="ring-deco" width="308" height="309" viewBox="0 0 308 309" aria-hidden="true">
      <circle cx="154" cy="154" r="134" fill="none" stroke="var(--teal-soft)" stroke-width="20"/>
    </svg>

    <div class="front-mark">
      <span class="front-mark__name">TOM VARULEK</span>
    </div>
    <p class="front-url">www.<span class="accent">tomvarulek</span>.net</p>
  </section>
</main>
</body>
</html>
```